OBK Farcoast Logistics Limited

We need the buissnes card to be very exclusive. As we are all young in our company. We need this to be the gate to make our clients feel deep interest for us.

We are focused in as International Trade advisors, and our products go from Oil Tanker Ships to Rubber balls for dogs.

Our Slogan is (omitted).
And our main marketing will be through Internet.

We were stablished in 2009 In Mexico and we also have offices in Hong Kong.
We have representatives in China and Europe.

Target Market(s)

Is every company or Individual that wants to develop an International Project or product development or Logistic service of Goods and people.
Some of our current projects are Ship Brokerage, Mine Brokerage, Real State and Product Pormotional development.

Industry/Entity Type

It Company

Requirements
Must have
• Our Logo and slogan, and make the card accoriding to the logo.
Nice to have
• Our Colors

```html
<!DOCTYPE html>
<html lang="en">
<head>
<meta charset="utf-8">
<title>OBK – Business Card</title>
<link rel="stylesheet" href="https://fonts.googleapis.com/css2?family=Open+Sans:wght@400;600;700&display=swap">
<style>
  :root {
    --page-bg: #e4e4e8;
    --card-dark: #2a2a2c;
    --card-mid: #4a4a4d;
    --brand-green: #7ccb2f;
    --brand-blue: #1a86c0;
    --brand-blue-deep: #0f6fa6;
    --text-light: #f2f2f2;
    --divider: rgba(255,255,255,0.25);
  }
  * { margin: 0; padding: 0; box-sizing: border-box; }
  html, body {
    width: 1200px; height: 987px; overflow: hidden;
    background: var(--page-bg);
    font-family: "Open Sans", sans-serif;
  }
  .card {
    position: absolute; left: 250px;
    width: 700px; height: 400px;
    border-radius: 26px; overflow: hidden;
    background:
      repeating-linear-gradient(90deg, rgba(255,255,255,0.035) 0 1px, transparent 1px 3px),
      linear-gradient(160deg, var(--card-mid) 0%, var(--card-dark) 60%, #1e1e20 100%);
    box-shadow: 0 10px 30px rgba(0,0,0,0.22);
  }
  .card-back { top: 60px; }
  .card-front { top: 527px; }

  .brand { position: absolute; display: flex; align-items: center; gap: 14px; }
  .brand-dot { width: 26px; height: 26px; border-radius: 50%; background: var(--brand-blue); }
  .brand-name { color: var(--brand-green); font-weight: 700; letter-spacing: 2px; line-height: 1; }

  .card-back .brand { left: 0; right: 0; top: 120px; justify-content: center; }
  .card-back .brand-name { font-size: 78px; }
  .card-back .web { position: absolute; left: 0; right: 0; top: 280px;
    text-align: center; color: var(--text-light); font-size: 22px; letter-spacing: 5px; }

  .card-front .brand { left: 50px; top: 80px; width: 240px; justify-content: center; }
  .card-front .brand-name { font-size: 62px; }

  .band { position: absolute; inset: 0; }
  .divider { position: absolute; left: 330px; top: 50px; width: 1px; height: 200px; background: var(--divider); }

  .contact { position: absolute; left: 360px; top: 52px; color: var(--text-light); }
  .contact-name { color: var(--brand-green); font-size: 25px; font-weight: 700; line-height: 1.1; }
  .contact-title { font-size: 17px; margin-bottom: 14px; }
  .contact-line { display: flex; align-items: center; gap: 8px; font-size: 18px; line-height: 1.45; }
  .contact-line svg { width: 15px; height: 15px; flex: none; }
  .contact-address { font-size: 18px; line-height: 1.3; margin-top: 10px; }
</style>
</head>
<body>

<section class="card card-back" aria-label="Card back">
  <div class="brand"><span class="brand-dot"></span><span class="brand-name">OBK</span></div>
  <p class="web">www.obkworldlink.net</p>
</section>

<section class="card card-front" aria-label="Card front">
  <svg class="band" viewBox="0 0 700 400" width="700" height="400">
    <defs>
      <linearGradient id="bandFill" x1="0" y1="0" x2="1" y2="1">
        <stop offset="0" stop-color="var(--brand-blue)"/>
        <stop offset="1" stop-color="var(--brand-blue-deep)"/>
      </linearGradient>
      <path id="webCurve" d="M30,245 C150,300 300,360 430,410"/>
    </defs>
    <path d="M0,190 C170,250 360,340 500,400 L0,400 Z" fill="url(#bandFill)"/>
    <path d="M0,170 C180,235 390,330 540,400" fill="none" stroke="var(--brand-green)" stroke-width="4"/>
    <text fill="#ffffff" font-family="Open Sans, sans-serif" font-size="21" letter-spacing="5">
      <textPath href="#webCurve">www.obkworldlink.net</textPath>
    </text>
  </svg>

  <div class="brand"><span class="brand-dot"></span><span class="brand-name">OBK</span></div>

  <div class="divider"></div>

  <div class="contact">
    <p class="contact-name">Your Name</p>
    <p class="contact-title">Title</p>
    <p class="contact-line">
      <svg viewBox="0 0 16 16" aria-hidden="true"><circle cx="8" cy="8" r="7" fill="none" stroke="var(--brand-green)" stroke-width="1.5"/><path d="M5.5 4.5 L7 6 L6 7.2 Q7 9 8.8 10 L10 9 L11.5 10.5 L10.5 11.8 Q6 11 4.2 5.5 Z" fill="var(--brand-green)"/></svg>
      123-456-0789
    </p>
    <p class="contact-line">
      <svg viewBox="0 0 16 16" aria-hidden="true"><rect x="4" y="1" width="8" height="14" rx="1.5" fill="var(--brand-green)"/><rect x="5.5" y="3" width="5" height="5" fill="#2a2a2c"/></svg>
      123-456-0789
    </p>
    <p class="contact-line">
      <svg viewBox="0 0 16 16" aria-hidden="true"><rect x="1" y="3" width="14" height="10" rx="1" fill="var(--brand-green)"/><path d="M1.5 3.5 L8 9 L14.5 3.5" fill="none" stroke="#2a2a2c" stroke-width="1.3"/></svg>
      hello@obkworldlink.net
    </p>
    <p class="contact-address">Street Name, City Name<br>State Zip Code</p>
  </div>
</section>

</body>
</html>
```